BOLD PINE HEATING AND COOLING

Industry/Entity Type

Hvac

Requirements
Must have
• logo
My name: Gavin Pruszynski
Phone number 555-309-4461
Text:
Furnace and AC repairs
New furnace and AC installation
Ductwork
Gas lines
Water Tanks
Tankless water heaters
Nice to have
• Profesional modern look

```html
<!DOCTYPE html>
<html lang="en">
<head>
<meta charset="utf-8">
<title>Bold Pine Heating and Cooling – Business Card</title>
<link href="https://fonts.googleapis.com/css2?family=Red+Hat+Display:wght@400;500;700&display=swap" rel="stylesheet">
<style>
  :root {
    --blue: #0a6fb1;
    --navy: #1a56a0;
    --red: #cf2027;
    --green: #6db33f;
    --paper: #f4f4f4;
    --grey: #6d6d6d;
    --ink: #2b2b2b;
    --backdrop: #e3e3e3;
  }
  * { box-sizing: border-box; margin: 0; padding: 0; }
  html, body { width: 1200px; height: 960px; overflow: hidden; }
  body {
    background: var(--backdrop);
    font-family: "Red Hat Display", Arial, sans-serif;
    position: relative;
  }
  .card {
    position: absolute;
    left: 312px;
    width: 578px;
    height: 330px;
    background: var(--paper);
    overflow: hidden;
  }
  .card--front { top: 125px; }
  .card--back { top: 505px; }

  .front-sky { position: absolute; left: 0; top: 0; width: 578px; height: 180px; }

  .brand {
    position: absolute;
    left: 0; width: 100%;
    text-align: center;
    color: var(--navy);
    font-weight: 700;
  }
  .brand__mark {
    display: block;
    margin: 0 auto 10px;
    width: 44px; height: 44px;
    border-radius: 50%;
    background: var(--navy);
  }
  .brand__name { display: block; font-size: 42px; letter-spacing: 1px; line-height: 1; }
  .brand__sub {
    display: flex; align-items: center; justify-content: center; gap: 8px;
    font-size: 15px; letter-spacing: 1px; margin-top: 6px; line-height: 1;
  }
  .brand__sub::before, .brand__sub::after {
    content: ""; width: 34px; height: 2px; background: var(--navy);
  }
  .card--front .brand { top: 82px; }
  .card--front .brand__mark { background: #fff; }
  .card--back .brand { top: 40px; }

  .front-rule { position: absolute; left: 0; top: 259px; width: 100%; height: 3px; background: var(--green); }
  .front-band {
    position: absolute; left: 0; top: 262px; width: 100%; height: 68px;
    background: var(--red);
    color: #fff; font-weight: 700; font-size: 19px;
    display: flex; align-items: center; justify-content: center; padding-top: 8px;
  }
  .web-pill {
    position: absolute; left: 184px; top: 247px; width: 210px; height: 27px;
    background: var(--green); border-radius: 7px;
    color: #fff; font-size: 16px; font-weight: 500;
    display: flex; align-items: center; justify-content: center;
  }

  .contact-row { position: absolute; left: 0; top: 196px; width: 100%; height: 70px; display: flex; }
  .contact-row__name {
    width: 288px; background: var(--blue); color: #fff;
    font-weight: 700; font-size: 19px;
    display: flex; align-items: center; justify-content: flex-end; padding-right: 16px;
  }
  .contact-row__details {
    flex: 1; margin-left: 2px; background: var(--red); color: #fff;
    font-size: 15px; display: flex; flex-direction: column; justify-content: center;
    padding-left: 20px; gap: 3px;
  }
  .contact-line { display: flex; align-items: center; gap: 5px; }
  .contact-line svg { width: 12px; height: 12px; fill: #fff; }

  .services {
    position: absolute; left: 0; top: 275px; width: 100%;
    text-align: center; color: var(--ink); font-size: 15px; line-height: 19px;
  }
  .services .sep { color: var(--red); }
  .back-stripe { position: absolute; left: 0; bottom: 0; width: 100%; height: 9px; background: var(--green); }
</style>
</head>
<body>

<section class="card card--front">
  <svg class="front-sky" viewBox="0 0 578 180" aria-hidden="true">
    <path d="M0 0 H578 V160 Q289 115 0 160 Z" fill="var(--blue)"/>
  </svg>
  <div class="brand">
    <span class="brand__mark"></span>
    <span class="brand__name">BOLD PINE</span>
    <span class="brand__sub">HEATING AND COOLING</span>
  </div>
  <div class="front-rule"></div>
  <div class="front-band">An Expert HVAC Contractor</div>
  <div class="web-pill">www.BoldPine-Air.ca</div>
</section>

<section class="card card--back">
  <div class="brand">
    <span class="brand__mark"></span>
    <span class="brand__name">BOLD PINE</span>
    <span class="brand__sub">HEATING AND COOLING</span>
  </div>
  <div class="contact-row">
    <div class="contact-row__name">Gavin Pruszynski</div>
    <div class="contact-row__details">
      <span class="contact-line">
        <svg viewBox="0 0 24 24" aria-hidden="true"><path d="M6.6 10.8a15.1 15.1 0 0 0 6.6 6.6l2.2-2.2c.3-.3.7-.4 1-.2 1.1.4 2.3.6 3.6.6.6 0 1 .4 1 1V20c0 .6-.4 1-1 1A17 17 0 0 1 3 4c0-.6.4-1 1-1h3.5c.6 0 1 .4 1 1 0 1.3.2 2.5.6 3.6.1.3 0 .7-.2 1z"/></svg>
        555-309-4461
      </span>
      <span class="contact-line">
        <svg viewBox="0 0 24 24" aria-hidden="true"><path d="M12 2a10 10 0 1 0 0 20 10 10 0 0 0 0-20zm6.9 6h-3a15.6 15.6 0 0 0-1.3-3.6A8 8 0 0 1 18.9 8zM12 4c.8 1.2 1.5 2.5 1.9 4h-3.8c.4-1.5 1.1-2.8 1.9-4zM4.3 14a8 8 0 0 1 0-4h3.4a16 16 0 0 0 0 4zm.8 2h3a15.6 15.6 0 0 0 1.3 3.6A8 8 0 0 1 5.1 16zm3-8h-3a8 8 0 0 1 4.3-3.6C8.8 5.6 8.4 6.8 8.1 8zM12 20c-.8-1.2-1.5-2.5-1.9-4h3.8c-.4 1.5-1.1 2.8-1.9 4zm2.3-6H9.7a14.7 14.7 0 0 1 0-4h4.6a14.7 14.7 0 0 1 0 4zm.3 5.6c.6-1.1 1-2.3 1.3-3.6h3a8 8 0 0 1-4.3 3.6zm1.7-5.6a16 16 0 0 0 0-4h3.4a8 8 0 0 1 0 4z"/></svg>
        www.boldpine-air.ca
      </span>
    </div>
  </div>
  <p class="services">
    Furnace &amp; AC Repairs <span class="sep">|</span> New Furnace &amp; AC Installation<br>
    Ductwork <span class="sep">|</span> Gas Lines <span class="sep">|</span> Water Tanks <span class="sep">|</span> Tankless Water Heaters
  </p>
  <div class="back-stripe"></div>
</section>

</body>
</html>
```